Tree Service Billboard 20x8 ft

We need a billboard design for a tree service company.
The billboard is 20ft x 8 ft so we need a design that is capable to stretching to those dimensions without loosing quality.
I have attached a series of images.
Image 1- Simply a billboard that I think looks good that I would like you to use for inspiration. I am aiming for the same format only no color in the wording, just black white, or gray. I like the the trees in the background, the logo placed to the left, and wording on the right.
Image 2- Current Logo I would like to the left of the billboard
Image 3- Another format of current logo if needed.
Image 4- A drawn out design template
Image 5- Another drawn out design template

Specific things I am looking for
-The contact number to be the largest thing on the design
-The logo on the design
-Key points to the design to say:
Tree Removal
Tree Trimming
Land Development
Stump Grinding
Storm Response
Insured
Free Bids
-The facebook logo
-The Google Logo

```html
<!DOCTYPE html>
<html lang="en">
<head>
<meta charset="utf-8">
<title>Birch Hollow Tree Service – Billboard</title>
<link rel="stylesheet" href="https://fonts.googleapis.com/css2?family=Oswald:wght@700&family=Rubik:wght@700;800&display=swap">
<style>
  :root {
    --stage: #2c3956;
    --board-white: #ffffff;
    --band-black: #000000;
    --ink: #111111;
    --brand-gray: #666666;
    --tick-gray: #777777;
    --emblem-ring: #5c5c5c;
    --emblem-fill: #1a1a1a;
    --on-dark: #ffffff;
  }
  * { margin: 0; padding: 0; box-sizing: border-box; }
  html, body {
    width: 1200px; height: 813px; overflow: hidden;
    background: var(--stage);
  }
  .billboard {
    position: absolute; left: 30px; top: 188px;
    width: 1140px; height: 436px;
    background: var(--board-white);
  }
  .brand-emblem {
    position: absolute; left: 145px; top: 45px;
    width: 164px; height: 164px; border-radius: 50%;
    background: var(--emblem-fill);
    border: 6px solid var(--emblem-ring);
  }
  .brand-name {
    position: absolute; left: 16px; top: 218px; width: 430px;
    text-align: center; white-space: nowrap;
    font-family: "Oswald", sans-serif; font-weight: 700;
    font-size: 33px; line-height: 50px; letter-spacing: -0.5px;
    color: var(--brand-gray); text-transform: uppercase;
  }
  .service-list { position: absolute; list-style: none; }
  .service-list--main { left: 469px; top: 49px; }
  .service-list--extra { left: 873px; top: 49px; }
  .service-item {
    display: flex; align-items: flex-start; gap: 11px;
    font-family: "Rubik", sans-serif; font-weight: 700;
    font-size: 28px; line-height: 33px; color: var(--ink);
    text-transform: uppercase; height: 62px; white-space: nowrap;
  }
  .service-list--extra .service-item:first-child { height: 95px; }
  .tick-box { flex: none; width: 34px; height: 34px; margin-top: 2px; }
  .contact-band {
    position: absolute; left: 0; bottom: 0; width: 100%; height: 126px;
    background: var(--band-black);
  }
  .phone-icon { position: absolute; left: 30px; top: 16px; width: 94px; height: 94px; }
  .phone-number {
    position: absolute; left: 144px; top: 0;
    font-family: "Rubik", sans-serif; font-weight: 800;
    font-size: 88px; line-height: 126px; letter-spacing: 0;
    color: var(--on-dark); white-space: nowrap;
  }
  .social-spot {
    position: absolute; top: 19px; width: 88px; height: 88px;
    border-radius: 50%; border: 4px solid var(--on-dark);
  }
  .social-spot--first { left: 888px; }
  .social-spot--second { left: 995px; }
</style>
</head>
<body>
  <main class="billboard">
    <div class="brand-emblem"></div>
    <div class="brand-name">Birch Hollow Tree Service</div>

    <ul class="service-list service-list--main">
      <li class="service-item"><svg class="tick-box" viewBox="0 0 34 34"><rect x="2" y="6" width="26" height="26" fill="none" stroke="var(--tick-gray)" stroke-width="3"/><path d="M7 18 L14 27 L31 2" fill="none" stroke="var(--ink)" stroke-width="4" stroke-linejoin="round"/></svg>Tree Removal</li>
      <li class="service-item"><svg class="tick-box" viewBox="0 0 34 34"><rect x="2" y="6" width="26" height="26" fill="none" stroke="var(--tick-gray)" stroke-width="3"/><path d="M7 18 L14 27 L31 2" fill="none" stroke="var(--ink)" stroke-width="4" stroke-linejoin="round"/></svg>Tree Trimming</li>
      <li class="service-item"><svg class="tick-box" viewBox="0 0 34 34"><rect x="2" y="6" width="26" height="26" fill="none" stroke="var(--tick-gray)" stroke-width="3"/><path d="M7 18 L14 27 L31 2" fill="none" stroke="var(--ink)" stroke-width="4" stroke-linejoin="round"/></svg>Land Development</li>
      <li class="service-item"><svg class="tick-box" viewBox="0 0 34 34"><rect x="2" y="6" width="26" height="26" fill="none" stroke="var(--tick-gray)" stroke-width="3"/><path d="M7 18 L14 27 L31 2" fill="none" stroke="var(--ink)" stroke-width="4" stroke-linejoin="round"/></svg>Stump Grinding</li>
    </ul>

    <ul class="service-list service-list--extra">
      <li class="service-item"><svg class="tick-box" viewBox="0 0 34 34"><rect x="2" y="6" width="26" height="26" fill="none" stroke="var(--tick-gray)" stroke-width="3"/><path d="M7 18 L14 27 L31 2" fill="none" stroke="var(--ink)" stroke-width="4" stroke-linejoin="round"/></svg><span>Storm<br>Response</span></li>
      <li class="service-item"><svg class="tick-box" viewBox="0 0 34 34"><rect x="2" y="6" width="26" height="26" fill="none" stroke="var(--tick-gray)" stroke-width="3"/><path d="M7 18 L14 27 L31 2" fill="none" stroke="var(--ink)" stroke-width="4" stroke-linejoin="round"/></svg>Insured</li>
      <li class="service-item"><svg class="tick-box" viewBox="0 0 34 34"><rect x="2" y="6" width="26" height="26" fill="none" stroke="var(--tick-gray)" stroke-width="3"/><path d="M7 18 L14 27 L31 2" fill="none" stroke="var(--ink)" stroke-width="4" stroke-linejoin="round"/></svg>Free Bids</li>
    </ul>

    <section class="contact-band">
      <svg class="phone-icon" viewBox="0 0 94 94">
        <path d="M18 8 C10 10 4 18 6 30 C10 52 36 80 60 88 C72 92 80 86 84 78 L70 64 C66 62 62 64 58 70 C46 64 32 50 26 38 C32 34 34 30 32 26 Z" fill="var(--on-dark)"/>
        <path d="M48 30 A14 14 0 0 1 62 44" fill="none" stroke="var(--on-dark)" stroke-width="6" stroke-linecap="round"/>
        <path d="M50 16 A28 28 0 0 1 78 44" fill="none" stroke="var(--on-dark)" stroke-width="6" stroke-linecap="round"/>
        <path d="M52 3 A40 40 0 0 1 91 42" fill="none" stroke="var(--on-dark)" stroke-width="6" stroke-linecap="round"/>
      </svg>
      <div class="phone-number">417-555-0148</div>
      <div class="social-spot social-spot--first"></div>
      <div class="social-spot social-spot--second"></div>
    </section>
  </main>
</body>
</html>
```